Lumira Skincare packaging designs

We are need to create packaging for our skincare brand. We need two designs. One for round jars which is for creams/capsules and the second will be for bottles/serums Some products will be larger in size so please ensure the packaging design will work and there isn't a lot white/empty space

Below are the names of some of our products.
Screw-On Top Jar (25 pads- 4 inches wide) - Velvet Swipes I Skin Brightening Pads
Pump Bottle (2 oz) - AquaLoft I Hyaluronic Acid + Vitamin Serum
Pump Bottle (6oz) - The Petal Wash I Conditioning Face Cleanser
Dropper bottle (1 oz) - Morning Mist I Hydrating Moisturizer
Cream jar (1.5 oz) - Morning Mist I Hydrating Moisturizer
Capsules Jar (25 capsules in a jar)- Plume Drop I Moisture + Hydrating Capsules
Capsules Jar (25 capsules in a jar) - Pure Pulse I Impurity Capsules

We will also need help with the packing design in terms of layout of the logo, item name, desc, and ingredients on each product.

Target Market(s)

women

Industry/Entity Type

skincare, beauty

Font styles to use
Sans Serif

Colors
E54698
E96AAD
F1A4CE
F9D9EA
FCEFF6

Requirements
Must have
• Pantone color is 2052 CP HEX #DAAFCA (218 , 175 , 202)

```html
<!DOCTYPE html>
<html lang="en">
<head>
<meta charset="utf-8">
<title>Lumira Skincare – The Petal Wash packaging</title>
<link href="https://fonts.googleapis.com/css2?family=Roboto+Condensed:wght@400;700&display=swap" rel="stylesheet">
<style>
  :root {
    --canvas: #f5f5f5;
    --rose: #dc6882;
    --rose-deep: #cb5670;
    --rose-box: #c97189;
    --rose-dusk: #9b5a6a;
    --white: #ffffff;
    --ink-soft: #f3f3f3;
  }
  * { box-sizing: border-box; margin: 0; padding: 0; }
  html, body { width: 1200px; height: 900px; overflow: hidden; }
  body {
    background: var(--canvas);
    font-family: "Roboto Condensed", "Arial Narrow", sans-serif;
    position: relative;
  }
  .label { position: absolute; background: var(--white); overflow: hidden; }
  .band {
    position: absolute; left: 0; right: 0; top: 0;
    background: var(--rose);
    display: flex; align-items: center; justify-content: center;
  }
  .brand {
    color: var(--white);
    font-weight: 400;
    letter-spacing: 0.18em;
    text-transform: uppercase;
    text-align: center;
    line-height: 1.15;
  }
  .title {
    color: var(--rose);
    font-weight: 700;
    text-transform: uppercase;
    line-height: 0.88;
    letter-spacing: -0.01em;
  }
  .tagline {
    color: var(--rose);
    text-transform: uppercase;
    letter-spacing: 0.2em;
    font-weight: 400;
  }
  .size-tag {
    position: absolute;
    background: var(--rose);
    color: var(--white);
    letter-spacing: 0.2em;
    display: flex; align-items: center; justify-content: center;
  }

  /* pump bottle label */
  .bottle-label { left: 87px; top: 357px; width: 262px; height: 400px; }
  .bottle-label .band { height: 144px; }
  .bottle-label .brand { font-size: 17px; }
  .bottle-label .title { position: absolute; left: 19px; top: 156px; font-size: 50px; }
  .bottle-label .tagline { position: absolute; left: 22px; top: 290px; font-size: 12.5px; }
  .bottle-label .size-tag { right: 0; top: 338px; width: 109px; height: 44px; font-size: 12px; }

  /* jar wrap strip */
  .jar-label { left: 415px; top: 570px; width: 270px; height: 57px; background: var(--white); }
  .jar-label .band { right: auto; width: 103px; height: 57px; background: var(--rose-dusk); }
  .jar-label .brand { font-size: 8px; }
  .jar-label .title { position: absolute; left: 109px; top: 4px; font-size: 17px; color: var(--rose-dusk); }
  .jar-label .tagline { position: absolute; left: 109px; top: 48px; font-size: 5px; color: var(--rose-dusk); }
  .jar-label .size-tag { right: 34px; top: 3px; width: 27px; height: 44px; font-size: 6px; background: var(--rose-box); }

  /* carton front */
  .box-front {
    position: absolute; left: 386px; top: 640px; width: 324px; height: 185px;
    background: var(--rose-box);
    display: flex; align-items: center; justify-content: center;
  }
  .box-front .contour { position: absolute; inset: 0; }
  .box-front .brand { position: relative; font-size: 24px; }

  /* tube */
  .tube-label { left: 690px; top: 153px; width: 248px; height: 682px; border-radius: 0 0 10px 10px; }
  .tube-label .band { height: 200px; background: var(--rose-deep); }
  .tube-label .brand { font-size: 20px; }
  .tube-label .title { position: absolute; left: 32px; top: 214px; font-size: 46px; }
  .tube-label .tagline { position: absolute; left: 37px; top: 340px; font-size: 11.5px; }
  .tube-label .size-tag { left: 159px; top: 462px; width: 51px; height: 42px; font-size: 10px; }

  /* dropper label */
  .dropper-label { left: 965px; top: 688px; width: 150px; height: 140px; }
  .dropper-label .band { height: 56px; }
  .dropper-label .brand { font-size: 8px; }
  .dropper-label .title { position: absolute; left: 10px; top: 64px; font-size: 19px; }
  .dropper-label .tagline { position: absolute; left: 10px; top: 124px; font-size: 5.5px; }
  .dropper-label .size-tag { right: 0; top: 64px; width: 18px; height: 40px; font-size: 5px; }
</style>
</head>
<body>

<section class="label bottle-label" aria-label="Pump bottle label">
  <div class="band"><p class="brand">Lumira<br>Skincare</p></div>
  <h1 class="title">The<br>Petal<br>Wash</h1>
  <p class="tagline">Conditioning face cleanser</p>
  <div class="size-tag">6 OZ</div>
</section>

<section class="label jar-label" aria-label="Jar wrap label">
  <div class="band"><p class="brand">Lumira<br>Skincare</p></div>
  <h2 class="title">The<br>Petal Wash</h2>
  <p class="tagline">Conditioning face cleanser</p>
  <div class="size-tag">6 OZ</div>
</section>

<section class="box-front" aria-label="Carton front">
  <svg class="contour" role="img" aria-label="Soft contour-line pattern in light rose" width="324" height="185">
    <rect width="324" height="185" fill="#c97189"/>
  </svg>
  <p class="brand">Lumira<br>Skincare</p>
</section>

<section class="label tube-label" aria-label="Tube label">
  <div class="band"><p class="brand">Lumira<br>Skincare</p></div>
  <h2 class="title">The<br>Petal<br>Wash</h2>
  <p class="tagline">Conditioning face cleanser</p>
  <div class="size-tag">6 OZ</div>
</section>

<section class="label dropper-label" aria-label="Dropper bottle label">
  <div class="band"><p class="brand">Lumira<br>Skincare</p></div>
  <h2 class="title">The<br>Petal Wash</h2>
  <p class="tagline">Conditioning face cleanser</p>
  <div class="size-tag">6OZ</div>
</section>

</body>
</html>
```